Sophisticated, clean website reflecting my feminine, playful side to sell my abstract art,

I need a website no more than 3 pages to showcase my paintings, a little about me and some contact info. I do abstracts so looking for something a little edgy, yet feminine and current.
Updates

Hi there, These are some artists websites that I Iike: Marnelvoss.com (I like how airy it is) peterwallombry.com garethpolvens.com (I like how it scrolls) I'll need a place for a photo ( a headshot-i do not have it yet so I'll need to be able to upload that later) as well as an area for my bio. Also, it's important that I will be able to upload any new photos and descriptions easily so it should be user friendly. Lastly, I like in a sunny place so would like to have this seem upbeat and playful as that is how i like to paint. thanks-I'm trying to upload my photos now -

Target Market(s)

ppl ages 35-70 who want large scale art for their homes

Industry/Entity Type

art

Coding

Coded - Design and coding required

Number of Pages Required

3 page

Colors

Designer to choose colors to be used in the design.

Requirements
Must have
• photos of my art, a place for my bio, be easy to reach me. tasteful-nothing too "in your face" -my clients are pretty high end and organized. They like clean lines
Nice to have
• sophisticated background, muted tones in the back-similar clean font throughout-no cursive
Should not have
• too many dark areas. Too many blocks of color. Too serious.

```html
<!DOCTYPE html>
<html lang="en">
<head>
<meta charset="utf-8">
<title>Helena Marsh — Abstract Art</title>
<link rel="stylesheet" href="https://fonts.googleapis.com/css2?family=Raleway:wght@300;400&family=Questrial&family=Nunito+Sans:wght@300&display=swap">
<style>
  :root {
    --ink: #3a3a3a;
    --ink-soft: #555;
    --line: #bdbdbd;
    --page: #f7f7f7;
    --header: #ffffff;
    --shadow: #cfcfcf;
    --icon: #8a8a8a;
  }
  * { margin: 0; padding: 0; box-sizing: border-box; }
  html, body { width: 1200px; height: 2802px; overflow: hidden; }
  body {
    position: relative;
    background: linear-gradient(180deg, #fbfbfb 0%, var(--page) 40%, #f5f5f5 100%);
    color: var(--ink);
    font-family: "Nunito Sans", sans-serif;
  }
  .abs { position: absolute; }

  /* Header */
  .site-header { position: absolute; left: 0; top: 0; width: 1200px; height: 99px; background: var(--header); border-bottom: 1px solid var(--line); }
  .brand { position: absolute; left: 0; top: 22px; width: 1200px; text-align: center; font-family: "Raleway", sans-serif; font-weight: 300; font-size: 44px; letter-spacing: 3px; color: var(--ink); }
  .brand-mark { display: inline-block; width: 22px; height: 22px; border: 2px solid var(--ink); margin: 0 14px; vertical-align: 6px; }
  .main-nav { position: absolute; top: 116px; left: 0; width: 1200px; height: 24px; font-family: "Questrial", sans-serif; font-size: 16px; color: var(--ink); }
  .main-nav a { position: absolute; transform: translateX(-50%); color: inherit; text-decoration: none; letter-spacing: .3px; }
  .main-nav .is-active::after { content: ""; position: absolute; left: 2px; right: 2px; bottom: -9px; height: 2px; background: var(--ink); }

  /* Hero */
  .hero-art { position: absolute; left: 0; top: 159px; width: 1200px; height: 657px;
    background:
      radial-gradient(ellipse at 30% 55%, rgba(20,24,24,.85) 0%, rgba(20,24,24,0) 40%),
      radial-gradient(ellipse at 85% 35%, rgba(235,232,220,.9) 0%, rgba(235,232,220,0) 35%),
      radial-gradient(ellipse at 15% 20%, rgba(186,96,38,.9) 0%, rgba(186,96,38,0) 35%),
      radial-gradient(ellipse at 60% 15%, rgba(186,96,38,.8) 0%, rgba(186,96,38,0) 30%),
      radial-gradient(ellipse at 90% 85%, rgba(40,130,115,.9) 0%, rgba(40,130,115,0) 35%),
      linear-gradient(120deg, #2f8f86 0%, #2a5d57 40%, #6d5a3a 70%, #c9b98a 100%); }
  .arrow { position: absolute; }

  /* Sections */
  .section-title { position: absolute; font-family: "Raleway", sans-serif; font-weight: 400; font-size: 46px; color: var(--ink); text-align: center; line-height: 1; }
  .title-rule { position: absolute; height: 2px; background: var(--ink); }

  .portrait-shadow { position: absolute; left: 94px; top: 967px; width: 355px; height: 374px; background: var(--shadow); }
  .portrait { position: absolute; left: 76px; top: 949px; width: 365px; height: 383px; background: radial-gradient(ellipse at 50% 45%, #d9d3ce 0%, #e9e7e5 35%, #f3f3f3 70%); }
  .bio { position: absolute; left: 490px; top: 1042px; width: 630px; text-align: center; font-size: 18.5px; line-height: 32px; color: var(--ink-soft); font-weight: 300; }
  .bio p + p { margin-top: 14px; }

  .gallery-shadow { position: absolute; left: 192px; top: 1610px; width: 841px; height: 533px; background: var(--shadow); }
  .gallery-art { position: absolute; left: 181px; top: 1598px; width: 841px; height: 533px;
    background:
      radial-gradient(ellipse at 22% 22%, rgba(196,150,40,.75) 0%, rgba(196,150,40,0) 28%),
      radial-gradient(ellipse at 75% 45%, rgba(30,60,140,.55) 0%, rgba(30,60,140,0) 32%),
      radial-gradient(ellipse at 65% 50%, rgba(214,170,90,.7) 0%, rgba(214,170,90,0) 25%),
      radial-gradient(ellipse at 18% 90%, rgba(180,70,30,.75) 0%, rgba(180,70,30,0) 28%),
      radial-gradient(ellipse at 45% 75%, rgba(110,170,215,.55) 0%, rgba(110,170,215,0) 35%),
      linear-gradient(135deg, #efe9dc 0%, #e6ecf2 55%, #e9e2d6 100%); }

  .contact-lead { position: absolute; left: 0; top: 2345px; width: 1200px; text-align: center; font-size: 20px; color: var(--ink-soft); font-weight: 300; }
  .contact-item { position: absolute; top: 2453px; width: 300px; transform: translateX(-50%); text-align: center; }
  .contact-icon { display: block; margin: 0 auto; width: 76px; height: 76px; }
  .contact-label { display: block; margin-top: 23px; font-family: "Questrial", sans-serif; font-size: 19.5px; color: var(--ink); }

  .site-footer { position: absolute; left: 0; top: 2717px; width: 1200px; height: 85px; border-top: 1px solid var(--line); text-align: center; padding-top: 29px; font-family: "Questrial", sans-serif; font-size: 14.5px; color: var(--ink); }
</style>
</head>
<body>

<header class="site-header">
  <div class="brand">HELENA<span class="brand-mark"></span>MARSH</div>
</header>
<nav class="main-nav">
  <a class="is-active" style="left:271px">HOME</a>
  <a style="left:449px">ABOUT ME</a>
  <a style="left:641px">GALLERY</a>
  <a style="left:829px">CONTACT</a>
</nav>

<div class="hero-art" role="img" aria-label="Abstract painting with teal, orange, black and white brush strokes"></div>
<svg class="arrow" style="left:22px;top:440px" width="28" height="46" viewBox="0 0 28 46"><path d="M24 3 L4 23 L24 43" fill="none" stroke="#fff" stroke-width="4"/></svg>
<svg class="arrow" style="left:1136px;top:440px" width="28" height="46" viewBox="0 0 28 46"><path d="M4 3 L24 23 L4 43" fill="none" stroke="#fff" stroke-width="4"/></svg>

<section aria-label="About me">
  <div class="portrait-shadow"></div>
  <div class="portrait" role="img" aria-label="Artist headshot"></div>
  <h2 class="section-title" style="left:655px;top:956px;width:300px">ABOUT ME</h2>
  <div class="title-rule" style="left:688px;top:1011px;width:235px"></div>
  <div class="bio">
    <p>Lorem ipsum dolor sit amet, consectetur adipiscing elit, sed do eiusmod tempor incididunt ut labore et dolore magna aliqua.</p>
    <p>Ut enim ad minim veniam, quis nostrud exercitation Lorem ipsum dolor sit amet, consectetur adipiscing elit, sed do eiusmod tempor incididunt ut labore et dolore magna aliqua. Duis aute irure dolor in reprehenderit in voluptate velit esse cillum dolore eu fugiat nulla pariatur. Excepteur sint occaecat cupidatat non proident, sunt in culpa qui officia deserunt mollit anim id est laborum.Sed ut perspiciatis unde pariatur.</p>
  </div>
</section>

<section aria-label="Gallery">
  <h2 class="section-title" style="left:450px;top:1500px;width:300px">GALLERY</h2>
  <div class="title-rule" style="left:502px;top:1556px;width:193px"></div>
  <div class="gallery-shadow"></div>
  <div class="gallery-art" role="img" aria-label="Abstract painting with ochre swirls, blue and rust strokes on a pale ground"></div>
  <svg class="arrow" style="left:86px;top:1841px" width="28" height="48" viewBox="0 0 28 48"><path d="M24 3 L4 24 L24 45" fill="none" stroke="#333" stroke-width="4"/></svg>
  <svg class="arrow" style="left:1085px;top:1841px" width="28" height="48" viewBox="0 0 28 48"><path d="M4 3 L24 24 L4 45" fill="none" stroke="#333" stroke-width="4"/></svg>
</section>

<section aria-label="Contact">
  <h2 class="section-title" style="left:415px;top:2267px;width:400px">CONTACT ME</h2>
  <div class="title-rule" style="left:479px;top:2322px;width:276px"></div>
  <p class="contact-lead">Please get in touch with me on below details.</p>

  <div class="contact-item" style="left:201px">
    <svg class="contact-icon" viewBox="0 0 76 76"><circle cx="38" cy="38" r="36.5" fill="none" stroke="var(--icon)" stroke-width="1.5"/><rect x="20" y="27" width="36" height="24" fill="none" stroke="#444" stroke-width="1.6"/><path d="M20 27 L38 41 L56 27 M20 51 L33 37 M56 51 L43 37" fill="none" stroke="#444" stroke-width="1.6"/></svg>
    <span class="contact-label">info@helenamarsh.com</span>
  </div>
  <div class="contact-item" style="left:482px">
    <svg class="contact-icon" viewBox="0 0 76 76"><circle cx="38" cy="38" r="36.5" fill="none" stroke="var(--icon)" stroke-width="1.5"/></svg>
    <span class="contact-label">Photogram@hmarshart</span>
  </div>
  <div class="contact-item" style="left:761px">
    <svg class="contact-icon" viewBox="0 0 76 76"><circle cx="38" cy="38" r="36.5" fill="none" stroke="var(--icon)" stroke-width="1.5"/><path d="M26 22 L31 20 L36 30 L32 34 C34 40 37 43 42 45 L46 41 L56 46 L54 51 C50 56 40 53 33 46 C26 39 21 29 26 22 Z" fill="none" stroke="#444" stroke-width="1.6" stroke-linejoin="round"/></svg>
    <span class="contact-label">Call me (555) 014 2270</span>
  </div>
  <div class="contact-item" style="left:1041px">
    <svg class="contact-icon" viewBox="0 0 76 76"><circle cx="38" cy="38" r="36.5" fill="none" stroke="var(--icon)" stroke-width="1.5"/></svg>
    <span class="contact-label">Clipstream@hmpainter</span>
  </div>
</section>

<footer class="site-footer">© 2022 Helena Marsh &nbsp; All Rights Reserved</footer>

</body>
</html>
```